Business Card for a Jewellery Brand

Business card for an upscale jewellery brand. Attached is the brand logo and icon and color board. I am looking for two card versions: one for the founder and one is generic. The card should be elegant and convey upscale and premium feel. I am open to both square and rectangle card shapes.

Industry/Entity Type

Jewelry

Contact Information for Business Card

Two cards: (1) Sunela Parvaniya (Founder) (2) General
(1) Sunela Parvaniya card should have Name: Sunela Parvaniya, Title: Founder Email id: sunela@quiremo.com.au. Phone no: +61452913307
(2) Generic card should have Email id: info@quiremo.com.au. Phone no: +61436207518

Requirements
Must have
• Workmark
• ICON
• Phone no
• Email ID
• ABN: 58219740312 (Note: ABN is Business number in Australia)
• Website: www.quiremo.com.au
• Instagram: quiremo_jewellery
• Facebook: @quiremojewellery
Nice to have
• Tagline

```html
<!DOCTYPE html>
<html lang="en">
<head>
<meta charset="utf-8">
<title>Quiremo Business Cards</title>
<link rel="stylesheet" href="https://fonts.googleapis.com/css2?family=Roboto:wght@400;500&family=Roboto+Condensed:wght@500&display=swap">
<style>
  :root {
    --backdrop: #2a2a2a;
    --card-white: #f8f8f7;
    --blush: #e69a96;
    --blush-text: #e4908d;
    --ink: #474747;
    --muted: #7d7d7d;
    --divider: #9a9a9a;
    --white: #ffffff;
  }
  * { margin: 0; padding: 0; box-sizing: border-box; }
  html, body { width: 1200px; height: 960px; overflow: hidden; }
  body {
    position: relative;
    background: var(--backdrop);
    font-family: "Roboto", Arial, sans-serif;
  }
  .card {
    position: absolute;
    width: 600px;
    height: 342px;
  }
  .card--founder { left: 302px; top: 129px; background: var(--card-white); }
  .card--generic { left: 299px; top: 488px; background: var(--blush); }

  /* Founder card: brand block */
  .brand {
    position: absolute;
    left: 60px;
    top: 92px;
    width: 230px;
    text-align: center;
  }
  .brand__square {
    display: block;
    width: 80px;
    height: 80px;
    margin: 0 auto 34px;
    border: 4px solid var(--blush);
  }
  .brand__name {
    font-weight: 400;
    font-size: 34px;
    letter-spacing: 7px;
    color: var(--blush);
    line-height: 1;
  }
  .divider {
    position: absolute;
    left: 306px;
    top: 83px;
    width: 1.5px;
    height: 183px;
    background: linear-gradient(to bottom, transparent, var(--divider) 20%, var(--divider) 80%, transparent);
  }

  /* Founder card: contact block */
  .contact {
    position: absolute;
    left: 336px;
    top: 89px;
  }
  .contact__name {
    font-family: "Roboto Condensed", "Arial Narrow", sans-serif;
    font-weight: 500;
    font-size: 21px;
    color: var(--blush-text);
    line-height: 24px;
  }
  .contact__title {
    font-size: 16px;
    color: var(--muted);
    line-height: 22px;
    margin-bottom: 6px;
    font-weight: 500;
  }
  .contact__abn {
    font-size: 14.5px;
    color: var(--ink);
    line-height: 20px;
    margin-bottom: 6px;
  }
  .contact__list { list-style: none; }
  .contact__item {
    display: flex;
    align-items: center;
    font-size: 14px;
    color: var(--ink);
    line-height: 18.3px;
  }
  .contact__icon {
    width: 12px;
    height: 12px;
    margin-right: 10px;
    flex: none;
  }
  .contact__icon--plain { width: 10px; height: 10px; margin: 0 11px 0 1px; background: var(--blush); }

  /* Generic card */
  .generic__name {
    position: absolute;
    left: 0;
    right: 0;
    top: 124px;
    text-align: center;
    font-weight: 400;
    font-size: 52px;
    letter-spacing: 10px;
    color: var(--white);
  }
  .generic__contact {
    position: absolute;
    left: 0;
    right: 0;
    top: 222px;
    text-align: center;
    font-size: 14px;
    color: var(--white);
    letter-spacing: 0.3px;
  }
  .generic__sep { margin: 0 10px; }
  .tagline {
    position: absolute;
    left: 80px;
    top: 298px;
    width: 440px;
    display: flex;
    align-items: center;
    gap: 4px;
  }
  .tagline__line {
    flex: 1;
    height: 1.5px;
  }
  .tagline__line--left { background: linear-gradient(to right, transparent, var(--white)); }
  .tagline__line--right { background: linear-gradient(to left, transparent, var(--white)); }
  .tagline__text {
    font-size: 13px;
    color: var(--white);
    letter-spacing: 0.3px;
    white-space: nowrap;
  }
</style>
</head>
<body>

<section class="card card--founder" aria-label="Founder business card">
  <div class="brand">
    <span class="brand__square" aria-hidden="true"></span>
    <div class="brand__name">QUIREMO</div>
  </div>
  <div class="divider" aria-hidden="true"></div>
  <div class="contact">
    <div class="contact__name">Sunela Parvaniya</div>
    <div class="contact__title">Founder</div>
    <div class="contact__abn">ABN: 58219740312</div>
    <ul class="contact__list">
      <li class="contact__item">
        <svg class="contact__icon" viewBox="0 0 12 12" aria-hidden="true"><rect x="3" y="0.5" width="6" height="11" rx="1" fill="none" stroke="#e4908d" stroke-width="1.3"/><rect x="5" y="9.3" width="2" height="1" fill="#e4908d"/></svg>
        +61452913307
      </li>
      <li class="contact__item">
        <svg class="contact__icon" viewBox="0 0 12 12" aria-hidden="true"><rect x="0.5" y="2.5" width="11" height="7.5" fill="#e4908d"/><path d="M0.5 2.8 L6 7 L11.5 2.8" fill="none" stroke="#fff" stroke-width="1"/></svg>
        sunela@quiremo.com.au
      </li>
      <li class="contact__item">
        <svg class="contact__icon" viewBox="0 0 12 12" aria-hidden="true"><circle cx="6" cy="6" r="5.3" fill="none" stroke="#e4908d" stroke-width="1.3"/><ellipse cx="6" cy="6" rx="2.3" ry="5.3" fill="none" stroke="#e4908d" stroke-width="1"/><line x1="0.7" y1="6" x2="11.3" y2="6" stroke="#e4908d" stroke-width="1"/></svg>
        www.quiremo.com.au
      </li>
      <li class="contact__item">
        <span class="contact__icon contact__icon--plain" aria-hidden="true"></span>
        quiremo_jewellery
      </li>
      <li class="contact__item">
        <span class="contact__icon contact__icon--plain" aria-hidden="true"></span>
        @quiremojewellery
      </li>
    </ul>
  </div>
</section>

<section class="card card--generic" aria-label="Generic business card">
  <div class="generic__name">QUIREMO</div>
  <div class="generic__contact">
    info@quiremo.com.au<span class="generic__sep">|</span>+61436207518
  </div>
  <div class="tagline">
    <span class="tagline__line tagline__line--left"></span>
    <span class="tagline__text">LOVE IS IN THE AIR</span>
    <span class="tagline__line tagline__line--right"></span>
  </div>
</section>

</body>
</html>
```